Zvo Klinieken website for a maxillofacial surgery clinic

It's a website for a clinic for maxillofacial surgery in WordPress . The website doesn't need to be complicated but has to look professional. It needs to be in Dutch so i can give the texts. Similar websites are www.tandartsenpraktijkveldorm.nl or www.pbtspecialisten.nl. Pages would be sort of similar to https://hetcentrumvoorgezichtszorg.nl/ or https://wervelmondclinics.nl/. Those lasts are maxillofacial surgery clinic websites, but there are little more extensive.
I uploaded the logo. If this is not the proper quality i can upload the eps. Logo was made through pixelforum.

Target Market(s)

Patients who can find me and see information about the clinic

Industry/Entity Type

Healthcare

Coding

Coded - Design and coding required

Number of Pages Required

5+ page

Font styles to use
Other font styles liked:
• Something standard professional

Colors
0054AA
0677BA
7BADD7
CADEEF
E8F1F8

Requirements
Nice to have
• Something in line with the logo. I prefer a little dark like the darker logos but I'm not sure if that's professional. Logos bkvzo and rlpw are instances i'm registered to so they will have to be on the website too but small somewhere.

```html
<!DOCTYPE html>
<html lang="nl">
<head>
<meta charset="utf-8">
<title>Zvo Klinieken</title>
<link href="https://fonts.googleapis.com/css2?family=Montserrat:wght@500;600;700&family=Lato:wght@400;700&family=Roboto:wght@400;500&display=swap" rel="stylesheet">
<style>
:root{
  --blue:#2fa0dc;
  --blue-dark:#2a8fcf;
  --slate:#6a84a8;
  --ink:#222;
  --muted:#555;
  --pale:#eef6fc;
  --footer:#121212;
  --grad:linear-gradient(90deg,#2ea6e0,#6c85a6);
}
*{margin:0;padding:0;box-sizing:border-box}
html,body{width:1200px;height:3572px;overflow:hidden}
body{position:relative;font-family:'Lato',sans-serif;color:var(--ink);background:#fff}
.abs{position:absolute}
.btn{position:absolute;display:flex;align-items:center;justify-content:center;gap:8px;background:var(--grad);color:#fff;font-family:'Montserrat',sans-serif;font-weight:700;font-size:15px;border-radius:30px;box-shadow:0 4px 8px rgba(0,0,0,.2);text-transform:uppercase}
.btn .dot{width:14px;height:14px;border:2px solid #fff;border-radius:50%}
.h2{font-family:'Montserrat',sans-serif;font-weight:700;color:var(--blue);font-size:36px;text-transform:uppercase}

/* top bar */
.topbar{top:0;left:0;width:1200px;height:55px;background:var(--blue);color:#fff;font-family:'Montserrat',sans-serif;font-size:15px;font-weight:500}
.topbar span{position:absolute;top:18px;display:flex;align-items:center;gap:8px}
.topbar .sep{width:1px;height:14px;background:rgba(255,255,255,.7);top:21px}

/* header */
.header{top:55px;left:0;width:1200px;height:102px;background:#fff}
.logo-box{top:39px;left:111px;width:208px;height:133px;background:#fff;border-radius:22px;box-shadow:0 2px 10px rgba(0,0,0,.08);display:flex;align-items:center;justify-content:center;z-index:3}
.brand{font-family:'Montserrat',sans-serif;font-weight:700;color:var(--blue);font-size:24px;text-align:center;line-height:1.1}
.nav{top:97px;left:437px;display:flex;gap:34px;font-family:'Montserrat',sans-serif;font-size:14px;font-weight:500;color:#333}
.nav .active{color:var(--blue);font-weight:700;border-bottom:2px solid var(--blue);padding-bottom:2px}

/* hero */
.hero{top:157px;left:0;width:1200px;height:539px;background:linear-gradient(100deg,#3d3d3d 0%,#6e6a68 45%,#b39a8c 75%,#d9c5b6 100%)}
.hero h3{top:308px;left:111px;color:#fff;font-family:'Montserrat',sans-serif;font-weight:700;font-size:27px}
.hero h1{top:345px;left:106px;color:#fff;font-family:'Montserrat',sans-serif;font-weight:700;font-size:62px;letter-spacing:1px}
.hero p{top:433px;left:111px;color:#eee;font-size:15px;line-height:28px;width:380px}

/* services */
.svc-title{top:768px;left:0;width:1200px;text-align:center}
.svc-sub{top:852px;left:0;width:1200px;text-align:center;font-family:'Roboto',sans-serif;color:#666;font-size:17px}
.card{top:908px;width:308px;height:486px;background:#fff;box-shadow:0 2px 12px rgba(0,0,0,.1);text-align:center}
.card h4{margin-top:25px;font-family:'Montserrat',sans-serif;font-weight:500;font-size:19px;text-transform:uppercase}
.card .photo{width:214px;height:214px;border-radius:50%;margin:20px auto 0;border:4px solid #5c7ba5}
.card p{margin:22px auto 0;width:282px;font-size:14px;line-height:27.5px;color:#444}
.card .more{position:absolute;left:50%;transform:translateX(-50%);bottom:26px;width:148px;height:46px;border:3px solid #5c7ba5;border-radius:25px;font-family:'Montserrat',sans-serif;font-weight:600;font-size:14px;color:#5c7ba5;display:flex;align-items:center;justify-content:center;background:#fff}
.card.featured{background:linear-gradient(180deg,#2fa3de,#6b84a7)}
.card.featured h4{color:#fff;font-weight:700;font-size:22px;margin-top:24px}
.card.featured .photo{border-color:#fff}
.card.featured p{color:#fff;font-size:13.5px}
.card.featured .more{border-color:#fff}

/* about */
.about{top:1487px;left:0;width:1200px;height:534px;background:var(--pale)}
.about-brand{top:1660px;left:108px;width:420px;text-align:center;font-family:'Montserrat',sans-serif;font-weight:700;color:var(--blue);font-size:64px}
.about-title{top:1565px;left:576px}
.about-text{top:1640px;left:576px;width:510px;font-size:14.5px;line-height:30px;color:#333}
.about-text p+p{margin-top:30px}

/* budget */
.budget{top:2021px;left:0;width:1200px;height:549px;background:linear-gradient(90deg,#9aa6ae 0%,#b9c6ce 50%,#8aa3b3 100%)}
.budget-box{top:2111px;left:108px;width:531px;height:370px;background:#fff;text-align:center}
.budget-box .h2{margin-top:30px;font-size:38px}
.budget-box p{width:460px;margin:22px auto 0;font-size:15.5px;line-height:32.5px;color:#444}

/* testimonials */
.testi-title{top:2634px;left:0;width:1200px;text-align:center}
.avatar{border-radius:50%}
.quote{font-family:Georgia,serif;font-weight:700;color:#e5e5e5;font-size:200px;line-height:1}
.tname{top:2848px;left:0;width:1200px;text-align:center;font-family:'Roboto',sans-serif;font-weight:500;font-size:19px}
.tloc{top:2885px;left:0;width:1200px;text-align:center;font-family:'Montserrat',sans-serif;font-size:12px;color:#555}
.stars{top:2900px;left:0;width:1200px;text-align:center;color:#f5b323;font-size:31px;letter-spacing:1px}
.ttext{top:2948px;left:260px;width:680px;text-align:center;font-size:15px;line-height:30px;color:#333}

/* footer */
.footer{top:3160px;left:0;width:1200px;height:412px;background:var(--footer);color:#fff}
.fcol h5{font-family:'Montserrat',sans-serif;font-weight:500;font-size:16px;margin-bottom:20px}
.fcol li{list-style:none;font-size:15px;height:34.5px;display:flex;align-items:center;gap:10px}
.arrow{width:14px;height:14px;border-radius:50%;background:#fff;display:inline-flex;align-items:center;justify-content:center}
.social{width:28px;height:28px;border-radius:50%;background:#fff}
.contact-ic{width:31px;height:31px;border-radius:50%;background:#fff;display:flex;align-items:center;justify-content:center;flex:none}
</style>
</head>
<body>

<div class="abs topbar">
  <span style="left:545px">In
    <svg width="20" height="20" viewBox="0 0 20 20" fill="none" stroke="#fff" stroke-width="1.5"><circle cx="10" cy="10" r="8"/><ellipse cx="10" cy="10" rx="3.5" ry="8"/><path d="M2 10h16M3.5 6h13M3.5 14h13"/></svg>▾</span>
  <span class="sep" style="left:630px"></span>
  <span style="left:652px"><svg width="13" height="13" viewBox="0 0 24 24" fill="#fff"><path d="M6.6 10.8a15 15 0 006.6 6.6l2.2-2.2c.3-.3.7-.4 1-.2 1.1.4 2.3.6 3.6.6.6 0 1 .4 1 1V20c0 .6-.4 1-1 1A17 17 0 013 4c0-.6.4-1 1-1h3.5c.6 0 1 .4 1 1 0 1.2.2 2.4.6 3.6.1.3 0 .7-.2 1z"/></svg>+31 79 555 0142</span>
  <span class="sep" style="left:817px"></span>
  <span style="left:843px"><svg width="11" height="14" viewBox="0 0 24 32" fill="#fff"><path d="M12 0a12 12 0 00-12 12c0 9 12 20 12 20s12-11 12-20A12 12 0 0012 0zm0 17a5 5 0 110-10 5 5 0 010 10z"/></svg>Zvo Klinieken, Verenigde Staten</span>
</div>

<div class="abs header"></div>
<div class="abs logo-box"><div class="brand">Zvo<br>Klinieken</div></div>
<nav class="abs nav">
  <span class="active">THUIS</span><span>OVER ONS</span><span>DIENSTEN</span><span>SPECIALE AANBIEDINGEN</span>
</nav>
<div class="btn" style="top:86px;left:950px;width:139px;height:43px;font-size:14px">NEEM CONTACT</div>

<section class="abs hero" role="img" aria-label="Foto van een lachende patiënte bij een tandheelkundige controle"></section>
<h3 class="abs hero" style="background:none;height:auto;width:auto;top:308px;left:111px;color:#fff;font-family:'Montserrat',sans-serif;font-size:27px">WELKOM BIJ</h3>
<h1 class="abs" style="top:345px;left:106px;color:#fff;font-family:'Montserrat',sans-serif;font-weight:700;font-size:62px">ZVO KLINIEKEN</h1>
<p class="abs" style="top:433px;left:111px;color:#eee;font-size:15px;line-height:28px;width:380px">Itaque earum rerum hic tenetur a sapiente delectus, ut aut reiciendis voluptatibus maiores</p>
<div class="btn" style="top:509px;left:111px;width:251px;height:51px"><span class="dot"></span>EEN AFSPRAAK MAKEN</div>

<div class="abs svc-title h2">Onze diensten</div>
<div class="abs svc-sub">Temporibus autem quibusdam et aut officiis debitis aut rerum necessitatibus</div>

<svg class="abs" style="top:1165px;left:42px" width="30" height="22" viewBox="0 0 30 22" fill="none" stroke="#2fa0dc" stroke-width="2"><path d="M28 11H3M11 3L3 11l8 8"/></svg>
<svg class="abs" style="top:1165px;left:1133px" width="30" height="22" viewBox="0 0 30 22" fill="none" stroke="#2fa0dc" stroke-width="2"><path d="M2 11h25M19 3l8 8-8 8"/></svg>

<div class="abs card" style="left:111px">
  <h4>Kaakchirurgie</h4>
  <div class="photo" role="img" aria-label="Foto van een patiënt in de behandelstoel" style="background:linear-gradient(135deg,#dfe6ea,#9fb1bb)"></div>
  <p>Temporibus autem quibusdam et aut officiis debitis aut rerum necessitatibus saepe eveniet ut et voluptates repudiandae sint et molestiae non recusandae</p>
  <div class="more">LEES VERDER</div>
</div>
<div class="abs card featured" style="left:447px">
  <h4>Verwijspraktijk</h4>
  <div class="photo" role="img" aria-label="Foto van een lachend kind bij de tandarts" style="background:linear-gradient(135deg,#e8d9cf,#b49a8a)"></div>
  <p>Itaque earum rerum hic tenetur a sapiente delectus, ut aut reiciendis voluptatibus maiores alias consequatur aut perferendis doloribus asperiores repellat.</p>
  <div class="more">LEES VERDER</div>
</div>
<div class="abs card" style="left:781px">
  <h4>Verwijzer</h4>
  <div class="photo" role="img" aria-label="Foto van een tandarts die een patiënte behandelt" style="background:linear-gradient(135deg,#e4e7ec,#a9b3c2)"></div>
  <p>Autem quibusdam et aut officiis debitis aut rerum necessitatibus saepe eveniet ut et voluptates repudiandae sint et molestiae non recusandae</p>
  <div class="more">LEES VERDER</div>
</div>

<section class="abs about"></section>
<div class="abs about-brand">Zvo Klinieken</div>
<div class="abs about-title h2">Over ons Zvo Klinieken</div>
<div class="abs about-text">
  <p>Nam libero tempore, cum soluta nobis est eligendi optio cumque nihil impedit voluptas assumenda est, omnis dolor repellendus. Temporibus autem quibusdam et aut officiis debitis aut rerum necessitatibus saepe eveniet ut et voluptates repudiandae sint et molestiae non recusandae.</p>
  <p>Itaque earum rerum hic tenetur a sapiente delectus, ut aut reiciendis voluptatibus maiores alias consequatur aut perferendis doloribus asperiores repellat.</p>
</div>
<div class="btn" style="top:1901px;left:576px;width:173px;height:51px"><span class="dot"></span>BEKIJK MEER</div>

<section class="abs budget" role="img" aria-label="Foto van chirurgen tijdens een operatie"></section>
<div class="abs budget-box">
  <div class="h2">Bespaar uw budget</div>
  <p>Temporibus autem quibusdam et aut officiis debitis aut rerum udiandae sint et molestiae non recusandae.</p>
  <p style="margin-top:32px">Itaque earum rerum hic tenetur a sapiente delectus, ut aut tur aut perferendis doloribus asperiores repellat.</p>
</div>
<div class="btn" style="top:2387px;left:251px;width:246px;height:51px"><span class="dot"></span>MAAK EEN AFSPRAAK</div>

<div class="abs testi-title h2">Wat klant zegt</div>
<div class="abs avatar" role="img" aria-label="Portretfoto klant" style="top:2714px;left:548px;width:104px;height:104px;background:linear-gradient(135deg,#c9a489,#6d5547)"></div>
<div class="abs avatar" role="img" aria-label="Portretfoto klant" style="top:2766px;left:118px;width:67px;height:67px;background:linear-gradient(135deg,#b99a86,#5a4a40)"></div>
<div class="abs avatar" role="img" aria-label="Portretfoto klant" style="top:2692px;left:995px;width:47px;height:47px;background:linear-gradient(135deg,#d5c6bb,#8a7a70)"></div>
<div class="abs" style="top:2805px;left:362px;width:14px;height:14px;border-radius:50%;background:#8dc63f"></div>
<div class="abs" style="top:2767px;left:877px;width:7px;height:7px;border-radius:50%;background:#2fa0dc"></div>
<div class="abs quote" style="top:2850px;left:135px">“</div>
<div class="abs quote" style="top:2962px;left:960px">”</div>
<div class="abs tname">RUBEN VERHOEF</div>
<div class="abs tloc">Verenigde Staten</div>
<div class="abs stars">★★★★★</div>
<div class="abs ttext">Temporibus autem qpe eveniet ut et voluptates repudiandae sint et molestiae non recusandae. Itaque earum rerum hic tenetur a sapiente delectus, ut aut reiciendis voluptatibus maiores alias consequatur aut perferendis doloribus asperiores repellat.</div>
<div class="abs" style="top:3071px;left:573px;width:12px;height:12px;border-radius:50%;background:#cfd8ea"></div>
<div class="abs" style="top:3070px;left:593px;width:14px;height:14px;border-radius:50%;background:#2fa0dc"></div>
<div class="abs" style="top:3071px;left:615px;width:12px;height:12px;border-radius:50%;background:#cfd8ea"></div>

<footer class="abs footer"></footer>
<div class="abs brand" style="top:3268px;left:111px;width:190px;color:var(--blue);font-size:30px">Zvo<br>Klinieken</div>
<div class="abs" style="top:3384px;left:121px;display:flex;gap:23px">
  <span class="social"></span><span class="social"></span><span class="social"></span><span class="social"></span>
</div>

<div class="abs fcol" style="top:3230px;left:392px;color:#fff">
  <h5>SNELLE KOPPELINGEN</h5>
  <ul><li><span class="arrow"><svg width="8" height="8" viewBox="0 0 8 8"><path d="M1 4h5M4 1.5L6.5 4 4 6.5" stroke="#121212" stroke-width="1.4" fill="none"/></svg></span>Thuis</li>
  <li><span class="arrow"><svg width="8" height="8" viewBox="0 0 8 8"><path d="M1 4h5M4 1.5L6.5 4 4 6.5" stroke="#121212" stroke-width="1.4" fill="none"/></svg></span>Over</li>
  <li><span class="arrow"><svg width="8" height="8" viewBox="0 0 8 8"><path d="M1 4h5M4 1.5L6.5 4 4 6.5" stroke="#121212" stroke-width="1.4" fill="none"/></svg></span>Diensten</li>
  <li><span class="arrow"><svg width="8" height="8" viewBox="0 0 8 8"><path d="M1 4h5M4 1.5L6.5 4 4 6.5" stroke="#121212" stroke-width="1.4" fill="none"/></svg></span>Getuigenissen</li>
  <li><span class="arrow"><svg width="8" height="8" viewBox="0 0 8 8"><path d="M1 4h5M4 1.5L6.5 4 4 6.5" stroke="#121212" stroke-width="1.4" fill="none"/></svg></span>Neem contact</li></ul>
</div>
<div class="abs fcol" style="top:3230px;left:627px;color:#fff">
  <h5>HULPKOPPELINGEN</h5>
  <ul><li><span class="arrow"><svg width="8" height="8" viewBox="0 0 8 8"><path d="M1 4h5M4 1.5L6.5 4 4 6.5" stroke="#121212" stroke-width="1.4" fill="none"/></svg></span>FAQ</li>
  <li><span class="arrow"><svg width="8" height="8" viewBox="0 0 8 8"><path d="M1 4h5M4 1.5L6.5 4 4 6.5" stroke="#121212" stroke-width="1.4" fill="none"/></svg></span>Gebruiksvoorwaarden</li>
  <li><span class="arrow"><svg width="8" height="8" viewBox="0 0 8 8"><path d="M1 4h5M4 1.5L6.5 4 4 6.5" stroke="#121212" stroke-width="1.4" fill="none"/></svg></span>Privacybeleid</li>
  <li><span class="arrow"><svg width="8" height="8" viewBox="0 0 8 8"><path d="M1 4h5M4 1.5L6.5 4 4 6.5" stroke="#121212" stroke-width="1.4" fill="none"/></svg></span>Ondersteuningskoppelingen</li>
  <li><span class="arrow"><svg width="8" height="8" viewBox="0 0 8 8"><path d="M1 4h5M4 1.5L6.5 4 4 6.5" stroke="#121212" stroke-width="1.4" fill="none"/></svg></span>Voorwaarden</li></ul>
</div>
<div class="abs fcol" style="top:3230px;left:884px;color:#fff;width:230px">
  <h5>NEEM CONTACT</h5>
  <div style="display:flex;gap:14px;font-size:15px;line-height:28px;margin-top:-2px">
    <span class="contact-ic"><svg width="12" height="16" viewBox="0 0 24 32" fill="#121212"><path d="M12 0a12 12 0 00-12 12c0 9 12 20 12 20s12-11 12-20A12 12 0 0012 0zm0 17a5 5 0 110-10 5 5 0 010 10z"/></svg></span>
    <span>Zvo Klinieken<br>Verenigde Staten</span></div>
  <div style="display:flex;gap:14px;align-items:center;font-size:15px;margin-top:16px">
    <span class="contact-ic"><svg width="14" height="14" viewBox="0 0 24 24" fill="#121212"><path d="M6.6 10.8a15 15 0 006.6 6.6l2.2-2.2c.3-.3.7-.4 1-.2 1.1.4 2.3.6 3.6.6.6 0 1 .4 1 1V20c0 .6-.4 1-1 1A17 17 0 013 4c0-.6.4-1 1-1h3.5c.6 0 1 .4 1 1 0 1.2.2 2.4.6 3.6.1.3 0 .7-.2 1z"/></svg></span>+31 79 555 0142</div>
  <div style="display:flex;gap:14px;align-items:center;font-size:15px;margin-top:21px">
    <span class="contact-ic"><svg width="15" height="12" viewBox="0 0 20 16" fill="#121212"><path d="M0 2a2 2 0 012-2h16a2 2 0 012 2v.5L10 9 0 2.5zM0 5l10 6.5L20 5v9a2 2 0 01-2 2H2a2 2 0 01-2-2z"/></svg></span>info@zvoklinieken.nl</div>
</div>

<div class="abs" style="top:3474px;left:108px;width:977px;height:1px;background:#777"></div>
<div class="abs" style="top:3477px;left:1126px;color:#fff;font-size:11px;font-family:'Roboto',sans-serif">C52</div>
<div class="abs" style="top:3523px;left:0;width:1200px;text-align:center;color:#fff;font-size:15px">Copyrights@2023.Zvo Klinieken.Alle rechten voorbehouden</div>

</body>
</html>
```